Design and Renovation Company Luxury Business Card

I want to create a luxury business card for a Design and Renovation Firm . We will use our current logo. The company name is 528BUILDA. We do not want anything standard. We need a very unique concept.
Please see uploaded inspiration. I really like the textured paper option. I would like the card to be thick with debossing, and/or embossing options. The logo has orange in it but I would like to see the card with and without the orange. I think the orange may make the company feel less high-end. The goal is to elevate the logo not match its vibe per se of the logo. We want something very unique, not standard at all!
I would like a space for :
Logo,
Name,
Position,
Email,
Office number,
Website Address,
Business Address,
Thank you!
Have fun!
Target Market(s)
Home owners Age 35 +
Industry/Entity Type
Design and Renovation
Contact Information for Business Card
Logo, Name, Position, Email, Office number, Website Address, Business Address,.
Colors
Designer to choose colors to be used in the design.
Requirements
Must have
- A luxury designer feel. Must be black or dark grey but open to other luxury ideas.
Nice to have
- Gold, silver, black embossing or debossing. Textured paper design.
Should not have
- A cheap look and feel.

```html
<!DOCTYPE html>
<html lang="en">
<head>
<meta charset="utf-8">
<title>528BUILDA Business Card</title>
<link href="https://fonts.googleapis.com/css2?family=Jost:wght@400;500;600&display=swap" rel="stylesheet">
<style>
  :root {
    --backdrop: #a6a6a6;
    --card-black: #000000;
    --accent-orange: #f39322;
    --stripe-white: #ffffff;
    --foil-gold: #e2c45c;
  }
  * { margin: 0; padding: 0; box-sizing: border-box; }
  html, body {
    width: 940px;
    height: 1200px;
    overflow: hidden;
    background: var(--backdrop);
    font-family: "Jost", "Futura", sans-serif;
  }
  .canvas {
    position: relative;
    width: 940px;
    height: 1200px;
  }
  .card {
    position: absolute;
    top: 250px;
    width: 400px;
    height: 700px;
    background: var(--card-black);
    overflow: hidden;
  }
  .card--front { left: 62px; }
  .card--back { left: 478px; }

  /* Plain edge bands */
  .edge-band {
    position: absolute;
    top: 0;
    height: 700px;
  }
  .edge-band--orange { left: 0; background: var(--accent-orange); }
  .edge-band--white { background: var(--stripe-white); }
  .card--front .edge-band--orange { width: 10px; }
  .card--front .edge-band--white { left: 16px; width: 4px; }
  .card--back .edge-band--orange { width: 10px; }
  .card--back .edge-band--white { left: 14px; width: 2px; }

  /* Front */
  .brand-name {
    position: absolute;
    left: 20px;
    right: 0;
    top: 332px;
    text-align: center;
    color: var(--stripe-white);
    font-weight: 500;
    font-size: 30px;
    letter-spacing: 3px;
    line-height: 1;
  }

  /* Back */
  .contact {
    position: absolute;
    left: 34px;
    color: var(--foil-gold);
  }
  .contact__company {
    top: 72px;
    font-size: 34px;
    font-weight: 500;
    letter-spacing: 3.5px;
    line-height: 1;
  }
  .contact__tagline {
    top: 111px;
    font-size: 11px;
    font-weight: 600;
    letter-spacing: 0.2px;
  }
  .contact__position {
    top: 131px;
    font-size: 11px;
    font-weight: 600;
  }
  .contact__details {
    top: 316px;
    font-size: 15px;
    line-height: 23px;
  }
  .contact__online {
    top: 574px;
    font-size: 14.5px;
    line-height: 24px;
  }
</style>
</head>
<body>
<main class="canvas">

  <section class="card card--front" aria-label="Card front">
    <div class="edge-band edge-band--orange"></div>
    <div class="edge-band edge-band--white"></div>
    <div class="brand-name">528BUILDA</div>
  </section>

  <section class="card card--back" aria-label="Card back">
    <div class="edge-band edge-band--orange"></div>
    <div class="edge-band edge-band--white"></div>
    <div class="contact contact__company">528BUILDA</div>
    <div class="contact contact__tagline">DESIGN AND RENOVATION FIRM</div>
    <div class="contact contact__position">CEO</div>
    <div class="contact contact__details">
      <p>+ 1234567890</p>
      <p>Dummy City, Dummy Country</p>
    </div>
    <div class="contact contact__online">
      <p>info@528buildadesignstudio.com</p>
      <p>www.528buildadesignstudio.com</p>
    </div>
  </section>

</main>
</body>
</html>
```